Flyer-Design für Musikverein - Jugendkapelle
Zielgruppe
Musikverein Kolmsried
Unsere Zielgruppe sind Kinder und Jugendliche, die ein Instrument erlernen wollen.
Der Einstieg der jüngsten geht in einem Alter ab ca. 8 Jahren los. Die meisten neuen Musiker steigen zwischen 10 - 14 Jahren ein.
Der Flyer soll aber auch geeignet sein um an Grund- und weiterführenden Schulen ausgelegt werden zu können um Musiker für die Jugendkapelle zu gewinnen. Dementsprechend frisch und interessant soll der Flyer gestaltet sein.
Aufgabenstellung
Es soll ansprechend sein für Jugendliche, frisch, fröhlich und soll das Interesse der jugendlichen mit dem Design wecken.
Es soll die Jugendlichkeit, die Blasmusik und das Vereinsleben miteinander verbinden, sowie die Vorteile und der Spaß an der Musik (Instrument erlernen, Spaß am Musizieren, neue Freunde und Kameradschaft und auch Freizeitaktivitäten) miteinander darstellen.

```html
<!DOCTYPE html>
<html lang="de">
<head>
<meta charset="utf-8">
<title>Jugendkapelle TAKTWERK – Musikverein Kolmsried</title>
<link rel="stylesheet" href="https://fonts.googleapis.com/css2?family=Work+Sans:wght@400;800&family=Caveat+Brush&display=swap">
<style>
  :root {
    --bg: #3d88c8;
    --paper: #5ba6dc;
    --text: #ffffff;
    --accent-light: #a9d4f3;
    --yellow: #fcc72c;
    --icon: #dce8f6;
  }
  html, body { margin: 0; padding: 0; overflow: hidden; }
  body {
    width: 1200px; height: 2572px;
    background: var(--bg);
    position: relative;
    font-family: "Work Sans", sans-serif;
    color: var(--text);
    letter-spacing: 0.03em;
  }
  .block { position: absolute; left: 109px; margin: 0; white-space: nowrap; }
  .intro { font-size: 42px; line-height: 52px; }
  .intro strong { font-weight: 800; letter-spacing: 0.01em; }
  .intro-1 { top: 162px; }
  .intro-2 { top: 421px; }
  .question { top: 707px; font-size: 46px; line-height: 61px; font-weight: 800; letter-spacing: 0.01em; }
  .invite { top: 1005px; font-size: 50px; line-height: 64px; font-weight: 800; color: var(--accent-light); letter-spacing: 0.01em; }
  .invite .band-name {
    background: var(--yellow); color: var(--text);
    padding: 4px 10px 6px 12px; margin-left: 4px;
  }
  .instrument-icon { position: absolute; left: 568px; top: 1253px; width: 97px; height: 149px; }
  .paper-patch { position: absolute; left: 0; top: 0; width: 1200px; height: 2572px; }
  .info-title {
    top: 1500px; font-family: "Caveat Brush", cursive; font-size: 100px; line-height: 120px;
    letter-spacing: 0; transform: scaleY(1.2); transform-origin: left top;
  }
  .contact { font-size: 42px; line-height: 52px; }
  .homepage { top: 1649px; }
  .homepage strong { font-weight: 800; letter-spacing: 0.01em; }
  .direct { top: 1874px; }
  .board-label { top: 2027px; font-weight: 800; font-size: 42px; letter-spacing: 0.01em; }
  .address { top: 2096px; line-height: 57px; }
  .reach { top: 2302px; line-height: 55px; }
  .greeting {
    position: absolute; left: 638px; top: 1968px; width: 462px; height: 152px;
    background: var(--yellow); transform: rotate(-7deg);
    font-family: "Caveat Brush", cursive; font-size: 80px; line-height: 64px;
    text-align: center; display: flex; align-items: center; justify-content: center;
    letter-spacing: 0.01em; white-space: nowrap;
  }
</style>
</head>
<body>
  <svg class="paper-patch" viewBox="0 0 1200 2572" aria-hidden="true">
    <polygon fill="var(--paper)" points="73,1587 190,1575 330,1610 520,1618 700,1650 900,1700 1080,1735 1200,1755 1200,2405 1150,2395 1000,2350 850,2320 700,2300 560,2290 480,2262 400,2150 300,2020 200,1880 140,1800 90,1785 95,1730 80,1660"/>
  </svg>

  <p class="block intro intro-1">In unserer Jugendkapelle haben die <strong>Kinder</strong><br><strong>und Jugendlichen</strong> die Möglichkeit, nach <strong>1 bis</strong><br><strong>2-jähriger Ausbildung</strong> in der Gruppe zu spie-<br>len und zu üben.</p>
  <p class="block intro intro-2">Danach geht es an das Musizieren im <strong>großen</strong><br><strong>Orchester.</strong> Letztendlich entscheiden die Diri-<br>genten und Ausbilder über den Eintritt in die<br>jeweiligen Orchester.</p>
  <p class="block question">Oder du kannst schon ein Instrument<br>spielen und willst mit anderen gemein-<br>sam musizieren?</p>
  <p class="block invite">Dann komm doch in die<br>Jugendkapelle<span class="band-name">„TAKTWERK“</span></p>

  <svg class="instrument-icon" viewBox="0 0 97 149" role="img" aria-label="Kleines Tuba-Symbol">
    <ellipse cx="48" cy="96" rx="40" ry="50" fill="var(--icon)"/>
  </svg>

  <h2 class="block info-title">Nähere Informationen:</h2>

  <p class="block contact homepage">auf unserer Homepage unter:<br><strong>www.kolmsried-musikverein-xz.de</strong></p>
  <p class="block contact direct">Oder kontaktiert<br>uns direkt:</p>
  <p class="block contact board-label">Jugendvorstand:</p>
  <p class="block contact address">Lena Morgental<br>Lindenhofweg<br>72999 Kolmsried</p>
  <p class="block contact reach">Tel.: 0170 0 00 12 34<br>E-Mail: lena.morgental@post-xz.de</p>

  <div class="greeting">Wir freuen uns<br>auf Euch!</div>
</body>
</html>
```